Create banners that convert viewers into buyers!

We provide Online Marketing Solutions for small to medium size businesses from web design, Local SEO, Pay-Per-Click, Social Media and Content Marketing. We've been helping local businesses since 2009 and offer a very high level of service that is rarely matched.

Really like to stay colors of logo like banner ad ideas 2 sample.

Would also like to use a photo of a responsive web design as attached image. (you may use a different layout as image provided may be to big for some dimensions)

Sizes needed:
728x90
300x250
480x60
Updates

Add Slogan: We Drive Traffic & Phone Calls!

Slogan: We Drive Phone Calls & Conversions

Target Market(s)

Small to Medium Size businesses: Main businesses we work with are Home Improvement, Lawyers & Physicians

Industry/Entity Type

Marketing

```html
<!DOCTYPE html>
<html lang="en">
<head>
<meta charset="utf-8">
<title>Northline Marketing – Banner Set</title>
<link href="https://fonts.googleapis.com/css2?family=Oswald:wght@500;700&family=Roboto+Condensed:wght@500;700&family=Tinos:wght@700&display=swap" rel="stylesheet">
<style>
  :root {
    --page: #e4edf8;
    --paper: #eef4fb;
    --navy: #16325c;
    --blue: #1f63c4;
    --blue-deep: #0d3f88;
    --blue-light: #3d8ee0;
    --frame: #1f2630;
    --white: #ffffff;
    --ink: #1b2430;
  }
  * { margin: 0; padding: 0; box-sizing: border-box; }
  html, body { width: 1200px; height: 715px; overflow: hidden; background: var(--page); }
  body { position: relative; font-family: "Roboto Condensed", sans-serif; }

  /* ---------- Leaderboard banner ---------- */
  .leaderboard {
    position: absolute; width: 1103px; height: 140px;
    background: linear-gradient(180deg, #f5f9fd, #dfe9f5);
    border: 2px solid var(--frame); overflow: hidden;
  }
  .leaderboard--large { left: 45px; top: 27px; }
  .leaderboard--small { left: 438px; top: 182px; transform: scale(0.644, 0.66); transform-origin: 0 0; }

  .brand-mini { position: absolute; left: 12px; top: 34px; width: 190px; text-align: center; color: var(--navy); font-weight: 700; }
  .brand-mini__name { display: flex; align-items: center; justify-content: center; gap: 6px; font-size: 27px; letter-spacing: 1px; line-height: 1; }
  .brand-mini__dot { width: 10px; height: 10px; border-radius: 50%; background: var(--navy); }
  .brand-mini__sub { font-size: 10px; letter-spacing: 5px; margin-top: 3px; }
  .site-url { position: absolute; left: 12px; top: 94px; width: 190px; text-align: center; font-size: 19px; font-weight: 500; color: var(--ink); }

  .shape { position: absolute; left: 0; top: 0; }
  .headline {
    position: absolute; left: 230px; top: 8px; width: 355px; height: 124px;
    display: flex; flex-direction: column; justify-content: center;
    font-family: "Oswald", sans-serif; font-weight: 700; color: var(--white);
    font-size: 33px; line-height: 38px; text-align: center; text-transform: uppercase;
    text-shadow: 0 2px 2px rgba(0,0,0,.35);
  }
  .checklist { position: absolute; left: 640px; top: 14px; list-style: none; }
  .checklist li {
    display: flex; align-items: center; gap: 9px; height: 22px;
    font-family: "Tinos", serif; font-weight: 700; font-size: 19px; color: var(--white);
  }
  .checklist svg { flex: none; }
  .devices-wide {
    position: absolute; left: 872px; top: 10px; width: 222px; height: 118px;
    background: radial-gradient(ellipse at 60% 45%, #5d6b7c, #2a323d 65%, #c9d3df 66%, #e3eaf3);
    border-radius: 6px;
  }

  /* ---------- Medium rectangle ---------- */
  .rectangle {
    position: absolute; left: 45px; top: 286px; width: 455px; height: 381px;
    background: linear-gradient(180deg, #f5f9fd, #dfe9f5);
    border: 2px solid var(--frame); overflow: hidden;
  }
  .rectangle .brand-mini { left: 0; top: 12px; width: 232px; }
  .rectangle .brand-mini__name { font-size: 32px; }
  .rectangle .brand-mini__sub { font-size: 12px; letter-spacing: 6px; }
  .stack-headline {
    position: absolute; left: 18px; top: 106px; width: 200px; text-align: center;
    font-family: "Oswald", sans-serif; font-weight: 700; color: var(--white);
    text-transform: uppercase; text-shadow: 0 2px 2px rgba(0,0,0,.35);
  }
  .stack-headline__lead { font-size: 27px; line-height: 36px; }
  .stack-headline__main { font-size: 44px; line-height: 50px; }
  .url-bar {
    position: absolute; left: 0; top: 330px; width: 232px; height: 49px;
    background: var(--blue-deep); color: var(--white);
    display: flex; align-items: center; justify-content: center; font-size: 20px; font-weight: 500;
  }
  .devices-tall {
    position: absolute; left: 236px; top: 6px; width: 212px; height: 128px;
    background: radial-gradient(ellipse at 55% 50%, #5f6d7e, #2a323d 62%, #c9d3df 63%, #e3eaf3);
    border-radius: 6px;
  }
  .service-panel {
    position: absolute; left: 232px; top: 138px; width: 221px; height: 172px;
    background: linear-gradient(180deg, var(--blue), var(--blue-deep));
  }
  .service-list { list-style: none; padding: 10px 0 0 12px; }
  .service-list li {
    display: flex; align-items: center; gap: 8px; height: 29px;
    font-family: "Oswald", sans-serif; font-weight: 500; font-size: 19px; color: var(--white); text-transform: uppercase;
  }
  .cta {
    position: absolute; left: 236px; top: 316px; width: 212px; height: 58px;
    display: flex; align-items: center; background: var(--white); border-radius: 4px; overflow: hidden;
  }
  .cta__icon { width: 56px; display: flex; justify-content: center; }
  .cta__label {
    flex: 1; height: 100%; background: var(--navy); color: var(--white);
    display: flex; align-items: center; justify-content: center;
    font-family: "Oswald", sans-serif; font-weight: 500; font-size: 22px; text-transform: uppercase;
  }

  /* ---------- Brand lockup ---------- */
  .brand-lockup { position: absolute; left: 557px; top: 420px; width: 595px; text-align: center; color: var(--navy); font-weight: 700; }
  .brand-lockup__name { display: flex; align-items: center; justify-content: center; gap: 14px; font-size: 84px; line-height: 1; letter-spacing: 3px; }
  .brand-lockup__dot { width: 22px; height: 22px; border-radius: 50%; background: var(--navy); }
  .brand-lockup__sub { font-size: 27px; letter-spacing: 16px; margin-top: 10px; }
</style>
</head>
<body>

  <!-- 728 x 90 leaderboard, shown twice at two sizes -->
  <section class="leaderboard leaderboard--large">
    <div class="brand-mini">
      <div class="brand-mini__name"><span class="brand-mini__dot"></span>NORTHLINE</div>
      <div class="brand-mini__sub">MARKETING</div>
    </div>
    <div class="site-url">www.YourSite.com</div>
    <svg class="shape" width="1103" height="140" viewBox="0 0 1103 140">
      <defs>
        <linearGradient id="hexFillA" x1="0" y1="0" x2="0" y2="1">
          <stop offset="0" stop-color="#2a74d0"/><stop offset="1" stop-color="#0d3f88"/>
        </linearGradient>
      </defs>
      <polygon points="604,8 835,8 866,70 835,130 604,130" fill="#1f5fbf"/>
      <polygon points="188,70 226,0 590,0 628,70 590,140 226,140" fill="#1f2630"/>
      <polygon points="200,70 234,8 582,8 616,70 582,132 234,132" fill="url(#hexFillA)"/>
    </svg>
    <h2 class="headline"><span>We Drive</span><span>Traffic &amp;</span><span>Phone Calls!</span></h2>
    <ul class="checklist">
      <li><svg width="14" height="14" viewBox="0 0 14 14"><circle cx="7" cy="7" r="7" fill="#fff"/><path d="M3.5 7.2 6 9.6 10.6 4.4" stroke="#16325c" stroke-width="2" fill="none"/></svg>Web Design</li>
      <li><svg width="14" height="14" viewBox="0 0 14 14"><circle cx="7" cy="7" r="7" fill="#fff"/><path d="M3.5 7.2 6 9.6 10.6 4.4" stroke="#16325c" stroke-width="2" fill="none"/></svg>Local SEO</li>
      <li><svg width="14" height="14" viewBox="0 0 14 14"><circle cx="7" cy="7" r="7" fill="#fff"/><path d="M3.5 7.2 6 9.6 10.6 4.4" stroke="#16325c" stroke-width="2" fill="none"/></svg>Pay-Per-Click</li>
      <li><svg width="14" height="14" viewBox="0 0 14 14"><circle cx="7" cy="7" r="7" fill="#fff"/><path d="M3.5 7.2 6 9.6 10.6 4.4" stroke="#16325c" stroke-width="2" fill="none"/></svg>Social Media</li>
      <li><svg width="14" height="14" viewBox="0 0 14 14"><circle cx="7" cy="7" r="7" fill="#fff"/><path d="M3.5 7.2 6 9.6 10.6 4.4" stroke="#16325c" stroke-width="2" fill="none"/></svg>Content Marketing</li>
    </ul>
    <div class="devices-wide" role="img" aria-label="Responsive website shown on desktop, tablet and phone"></div>
  </section>

  <section class="leaderboard leaderboard--small">
    <div class="brand-mini">
      <div class="brand-mini__name"><span class="brand-mini__dot"></span>NORTHLINE</div>
      <div class="brand-mini__sub">MARKETING</div>
    </div>
    <div class="site-url">www.YourSite.com</div>
    <svg class="shape" width="1103" height="140" viewBox="0 0 1103 140">
      <defs>
        <linearGradient id="hexFillB" x1="0" y1="0" x2="0" y2="1">
          <stop offset="0" stop-color="#2a74d0"/><stop offset="1" stop-color="#0d3f88"/>
        </linearGradient>
      </defs>
      <polygon points="604,8 835,8 866,70 835,130 604,130" fill="#1f5fbf"/>
      <polygon points="188,70 226,0 590,0 628,70 590,140 226,140" fill="#1f2630"/>
      <polygon points="200,70 234,8 582,8 616,70 582,132 234,132" fill="url(#hexFillB)"/>
    </svg>
    <h2 class="headline"><span>We Drive</span><span>Traffic &amp;</span><span>Phone Calls!</span></h2>
    <ul class="checklist">
      <li><svg width="14" height="14" viewBox="0 0 14 14"><circle cx="7" cy="7" r="7" fill="#fff"/><path d="M3.5 7.2 6 9.6 10.6 4.4" stroke="#16325c" stroke-width="2" fill="none"/></svg>Web Design</li>
      <li><svg width="14" height="14" viewBox="0 0 14 14"><circle cx="7" cy="7" r="7" fill="#fff"/><path d="M3.5 7.2 6 9.6 10.6 4.4" stroke="#16325c" stroke-width="2" fill="none"/></svg>Local SEO</li>
      <li><svg width="14" height="14" viewBox="0 0 14 14"><circle cx="7" cy="7" r="7" fill="#fff"/><path d="M3.5 7.2 6 9.6 10.6 4.4" stroke="#16325c" stroke-width="2" fill="none"/></svg>Pay-Per-Click</li>
      <li><svg width="14" height="14" viewBox="0 0 14 14"><circle cx="7" cy="7" r="7" fill="#fff"/><path d="M3.5 7.2 6 9.6 10.6 4.4" stroke="#16325c" stroke-width="2" fill="none"/></svg>Social Media</li>
      <li><svg width="14" height="14" viewBox="0 0 14 14"><circle cx="7" cy="7" r="7" fill="#fff"/><path d="M3.5 7.2 6 9.6 10.6 4.4" stroke="#16325c" stroke-width="2" fill="none"/></svg>Content Marketing</li>
    </ul>
    <div class="devices-wide" role="img" aria-label="Responsive website shown on desktop, tablet and phone"></div>
  </section>

  <!-- 300 x 250 medium rectangle -->
  <section class="rectangle">
    <div class="brand-mini">
      <div class="brand-mini__name"><span class="brand-mini__dot"></span>NORTHLINE</div>
      <div class="brand-mini__sub">MARKETING</div>
    </div>
    <svg class="shape" width="455" height="381" viewBox="0 0 455 381">
      <defs>
        <linearGradient id="shieldFill" x1="0" y1="0" x2="0" y2="1">
          <stop offset="0" stop-color="#2a74d0"/><stop offset="1" stop-color="#0d3f88"/>
        </linearGradient>
      </defs>
      <polygon points="6,96 30,74 206,74 230,96 230,304 206,330 30,330 6,304" fill="#1f2630"/>
      <polygon points="16,102 36,84 200,84 220,102 220,298 200,320 36,320 16,298" fill="url(#shieldFill)"/>
    </svg>
    <h2 class="stack-headline">
      <div class="stack-headline__lead">We Drive</div>
      <div class="stack-headline__main">Traffic &amp;</div>
      <div class="stack-headline__main">Phone</div>
      <div class="stack-headline__main">Calls!</div>
    </h2>
    <div class="url-bar">www.YourSite.com</div>
    <div class="devices-tall" role="img" aria-label="Responsive website shown on desktop, tablet and phone"></div>
    <div class="service-panel">
      <ul class="service-list">
        <li><svg width="9" height="12" viewBox="0 0 9 12"><path d="M1 1 7 6 1 11" stroke="#fff" stroke-width="2" fill="none"/></svg>Web Design</li>
        <li><svg width="9" height="12" viewBox="0 0 9 12"><path d="M1 1 7 6 1 11" stroke="#fff" stroke-width="2" fill="none"/></svg>Local SEO</li>
        <li><svg width="9" height="12" viewBox="0 0 9 12"><path d="M1 1 7 6 1 11" stroke="#fff" stroke-width="2" fill="none"/></svg>Pay-Per-Click</li>
        <li><svg width="9" height="12" viewBox="0 0 9 12"><path d="M1 1 7 6 1 11" stroke="#fff" stroke-width="2" fill="none"/></svg>Social Media</li>
        <li><svg width="9" height="12" viewBox="0 0 9 12"><path d="M1 1 7 6 1 11" stroke="#fff" stroke-width="2" fill="none"/></svg>Content Marketing</li>
      </ul>
    </div>
    <a class="cta">
      <span class="cta__icon"><svg width="34" height="34" viewBox="0 0 34 34"><circle cx="17" cy="17" r="15" fill="#16325c"/></svg></span>
      <span class="cta__label">Know More</span>
    </a>
  </section>

  <!-- Brand lockup -->
  <div class="brand-lockup">
    <div class="brand-lockup__name"><span class="brand-lockup__dot"></span>NORTHLINE</div>
    <div class="brand-lockup__sub">MARKETING</div>
  </div>

</body>
</html>
```